Cover Design Brief – Prayer Book (Modern Revision)

Design a new, modern, high-quality book cover that reflects the essence of the original version. The updated cover should feel contemporary yet familiar, appealing to both younger and older readers, while evoking a sense of spiritual depth, calm, and authenticity.

1. Visual Reference to the Original Cover
Continuity:
Retain visual elements such as the color palette, central motifs (eg, geometric patterns, Islamic ornaments, or a symbolic figure), and overall structure from the original cover.

Recognition:
Readers familiar with the old cover should instantly recognize the book but be pleasantly surprised by the refined, modern look.

2. Style & Mood
Modern Islamic design, minimalist and clean rather than ornate.

Spiritual, calming, elegant – avoid overly bright or flashy visuals.

Subtle use of Islamic motifs, possibly a decorative Arabic calligraphy word like ṣalāh (صلاة) to enrich the theme.

3. Suggested Color Palette
Deep blue, teal, petrol green, olive, sand tones, or midnight blue with accents of gold – depending on the original cover scheme.

Avoid neon or loud colors.

If gold or silver is used, it should be subtle and classy (eg, foil stamping or embossing, not digital effects).

4. Typography
A modern serif font for the main title is welcome, but it should be clean and elegant.

Subtitles should use a clear, legible font.

If the title includes Arabic text, it should be displayed in tasteful classical calligraphy or a stylized script.

5. Back Cover
Will include a brief description text (to be provided later).

Clean layout, optionally with a small publisher logo.

Possibly a short quote or ḥadīth in Arabic (with or without translation) to complement the design.

6. Target Audience
German-speaking Muslims, male and female, ages 15+

Suitable for both beginners and advanced practitioners of the prayer

Designed as a long-term spiritual companion and a thoughtful gift

```html
<!DOCTYPE html>
<html lang="de">
<head>
<meta charset="utf-8">
<title>As-ṣalāh – Das Gebet im Islam</title>
<link href="https://fonts.googleapis.com/css2?family=Poppins:wght@200;500&display=swap" rel="stylesheet">
<style>
  :root {
    --night: #0f1720;
    --sky-deep: #1c3a52;
    --sky-mid: #3e6a86;
    --dusk: #c9825a;
    --glow: #f3b064;
    --stone: #1a1c20;
    --ink: #ffffff;
  }
  html, body {
    margin: 0;
    padding: 0;
    width: 848px;
    height: 1200px;
    overflow: hidden;
    background: var(--night);
  }
  .cover {
    position: relative;
    width: 848px;
    height: 1200px;
    overflow: hidden;
    font-family: "Poppins", sans-serif;
    color: var(--ink);
  }
  .cover-scene {
    position: absolute;
    inset: 0;
    background:
      radial-gradient(ellipse 300px 220px at 50% 80%, var(--glow) 0%, var(--dusk) 35%, rgba(62,106,134,0) 100%),
      linear-gradient(90deg, var(--stone) 0%, var(--stone) 24%, rgba(26,28,32,0) 28%, rgba(26,28,32,0) 72%, var(--stone) 76%, var(--stone) 100%),
      linear-gradient(180deg, var(--night) 0%, var(--sky-deep) 30%, var(--sky-mid) 60%, var(--dusk) 78%, #5a2a22 86%, #2a1814 100%);
  }
  .emblem {
    position: absolute;
    left: 361px;
    top: 30px;
    width: 128px;
    height: 128px;
  }
  .title {
    position: absolute;
    left: 0;
    right: 0;
    top: 176px;
    margin: 0;
    text-align: center;
    font-weight: 200;
    font-size: 92px;
    line-height: 1;
    letter-spacing: 1px;
  }
  .subtitle {
    position: absolute;
    left: 213px;
    width: 422px;
    top: 292px;
    display: flex;
    align-items: center;
    gap: 12px;
    margin: 0;
    font-weight: 500;
    font-size: 23px;
    white-space: nowrap;
  }
  .subtitle::before,
  .subtitle::after {
    content: "";
    flex: 1;
    height: 1px;
    background: var(--ink);
    opacity: 0.8;
  }
  .edition {
    position: absolute;
    left: 17px;
    top: 1103px;
    margin: 0;
    font-weight: 500;
    font-size: 15px;
    line-height: 1.12;
  }
  .publisher {
    position: absolute;
    right: 40px;
    bottom: 24px;
    display: flex;
    flex-direction: column;
    align-items: center;
    gap: 10px;
  }
  .publisher-mark {
    width: 56px;
    height: 56px;
    border: 2px solid var(--ink);
    border-radius: 50%;
  }
  .publisher-name {
    font-weight: 500;
    font-size: 14px;
  }
</style>
</head>
<body>
  <main class="cover">
    <div class="cover-scene" role="img" aria-label="Foto: Mann kniet auf einem roten Gebetsteppich unter einem steinernen Torbogen und erhebt die Hände zum Bittgebet vor einem Sternenhimmel mit Sonnenuntergang"></div>

    <svg class="emblem" viewBox="0 0 128 128" role="img" aria-label="Arabische Kalligrafie des Wortes As-Salah in einem weißen Kreis">
      <circle cx="64" cy="64" r="62" fill="var(--ink)"/>
    </svg>

    <h1 class="title">As-ṣalāh</h1>
    <p class="subtitle">Das Gebet im Islam</p>

    <p class="edition">Vollstäandig<br>revidierte<br>Ausgabe</p>

    <div class="publisher">
      <span class="publisher-mark"></span>
      <span class="publisher-name">Lichtpfad Verlag</span>
    </div>
  </main>
</body>
</html>
```